Digital Marketing Agency Landing Page

At VELIM, we offer a comprehensive solution for solar companies' client acquisition needs in the rapidly growing industry. We handle end-to-end client acquisition, meaning we manage the entire lifecycle of capturing new clients—from initial lead generation to delivering the ready-to-buy homeowner. Our expertise in targeted advertising, data analytics, and customer relationship management ensures that we not only find potential customers but also nurture them through tailored engagement strategies until they are ready to make a purchase. By entrusting us with your client acquisition process, solar companies can focus on what they do best—providing sustainable energy solutions—while we work behind the scenes to grow your customer base and increase your market share.

We need to restructure our website to make it more professional. We don't need any complex functionalities. We are looking for someone that is good in design and can build a visually aesthetic website following our brand image. We only need a landing page and a lead form in the end. I would like to have only one page, but a relatively big one where people scroll down. I would like to have a minimal and classy look. Something that is timeless and elegant.

Structure:

initial page
About us
How we operate
Get in touch

Target Market(s)

Solar Comapanies

Industry/Entity Type

Marketing solautions

Coding

Coded - Design and coding required

Number of Pages Required

1 page

Requirements
Nice to have
• Inspirations: https://www.qz.zu/ https://www.marchbeck.example/ https://www.tovanrid.example/ https://pruvo.example/

```html
<!DOCTYPE html>
<html lang="en">
<head>
<meta charset="utf-8">
<title>VELIM — Client Acquisition for Solar Companies</title>
<link rel="stylesheet" href="https://fonts.googleapis.com/css2?family=Montserrat:wght@300;400;500&display=swap">
<style>
  :root {
    --navy: #10222f;
    --blue-line: #3f86c0;
    --cream: #ede8dc;
    --page: #f5f5f6;
    --text: #1b1b1b;
    --white: #ffffff;
  }
  * { box-sizing: border-box; margin: 0; padding: 0; }
  html, body { width: 1200px; height: 2655px; overflow: hidden; }
  body {
    position: relative;
    background: var(--page);
    font-family: 'Montserrat', sans-serif;
    color: var(--text);
  }
  .backdrop { position: absolute; inset: 0; }
  .site-header {
    position: absolute; top: 0; left: 0; width: 1200px; height: 122px;
    background: var(--navy); border-bottom: 4px solid var(--blue-line);
    z-index: 3;
  }
  .menu-icon { position: absolute; left: 113px; top: 50px; width: 32px; }
  .menu-icon span { display: block; height: 4px; background: var(--white); margin-bottom: 6px; border-radius: 1px; }
  .brand {
    position: absolute; color: var(--white);
    font-weight: 300; letter-spacing: 2px; line-height: 1;
  }
  .site-header .brand { left: 0; width: 1200px; text-align: center; top: 37px; font-size: 40px; }
  .pill {
    display: inline-flex; align-items: center; justify-content: center;
    background: var(--cream); color: var(--text); border-radius: 24px;
    font-size: 15px; font-weight: 400; height: 42px;
  }
  .site-header .pill { position: absolute; left: 960px; top: 39px; width: 130px; }
  .hero-visual { position: absolute; left: 0; top: 0; }
  .hero-title {
    position: absolute; left: 112px; top: 296px; color: var(--white);
    font-size: 50px; font-weight: 400; line-height: 52px; letter-spacing: 0.5px; z-index: 2;
  }
  .hero .pill { position: absolute; left: 112px; top: 421px; width: 130px; z-index: 2; }
  .quote-panel {
    position: absolute; left: 213px; top: 605px; width: 774px; height: 305px;
    background: var(--navy); border-radius: 40px; z-index: 2; text-align: center;
  }
  .quote-panel h2 { color: var(--white); font-size: 19px; font-weight: 300; margin-top: 38px; }
  .quote-fields { position: absolute; left: 143px; top: 87px; width: 494px; display: grid; grid-template-columns: 238px 238px; gap: 13px 17px; }
  .quote-fields div {
    height: 43px; border: 1px solid #c9ccd0; border-radius: 3px; color: #c9ccd0;
    font-size: 13px; text-align: left; padding: 13px 17px; font-weight: 300;
  }
  .quote-panel .pill { position: absolute; left: 324px; top: 213px; width: 130px; }
  .about-photo { position: absolute; left: 110px; top: 1098px; }
  .about-title { position: absolute; left: 605px; top: 1090px; font-size: 35px; font-weight: 300; }
  .about-copy {
    position: absolute; left: 600px; top: 1160px; width: 489px;
    font-size: 16.5px; line-height: 29px; font-weight: 300; text-align: justify; color: #222;
  }
  .about .pill { position: absolute; left: 593px; top: 1473px; width: 130px; }
  .services-title { position: absolute; left: 0; width: 1200px; top: 1682px; text-align: center; font-size: 35px; font-weight: 300; }
  .service { position: absolute; width: 300px; text-align: center; }
  .service svg { display: block; margin: 0 auto; }
  .service p { font-size: 23px; font-weight: 400; line-height: 29px; margin-top: 14px; }
  .site-footer { position: absolute; left: 0; top: 0; }
  .footer-content { position: absolute; left: 0; top: 2470px; width: 1200px; color: var(--white); }
  .site-footer-brand { left: 116px; top: 10px; font-size: 40px; }
  .footer-nav { position: absolute; left: 390px; top: 40px; display: flex; gap: 36px; font-size: 17px; font-weight: 300; }
  .social { position: absolute; left: 862px; top: 38px; display: flex; gap: 16px; }
  .social span {
    display: flex; align-items: center; gap: 6px; font-size: 12px; font-weight: 300;
  }
  .social span::before { content: ""; width: 22px; height: 22px; border-radius: 50%; background: var(--white); display: inline-block; }
  .footer-rule { position: absolute; left: 111px; top: 108px; width: 978px; height: 1px; background: #8896a0; }
  .copyright { position: absolute; left: 0; width: 1200px; top: 132px; text-align: center; font-size: 15px; font-weight: 300; }
</style>
</head>
<body>
  <svg class="backdrop" width="1200" height="2655" aria-hidden="true">
    <path d="M790 900 C840 1300 1100 1600 1200 1900 V900Z" fill="#fafafb"/>
    <path d="M0 1150 C200 1500 180 1900 420 2300 H0Z" fill="#ededee"/>
    <path d="M1200 1000 C1050 1300 1000 1800 1200 2200Z" fill="#efeff0"/>
  </svg>

  <header class="site-header">
    <div class="menu-icon"><span></span><span></span><span></span></div>
    <div class="brand">VELIM</div>
    <a class="pill">Contact Us</a>
  </header>

  <section class="hero">
    <svg class="hero-visual" width="1200" height="790">
      <defs>
        <linearGradient id="heroTone" x1="0" y1="0" x2="1" y2="0.4">
          <stop offset="0" stop-color="#0b1745"/>
          <stop offset="0.45" stop-color="#0c1c55"/>
          <stop offset="0.75" stop-color="#1c3c7a"/>
          <stop offset="1" stop-color="#3a5a8c"/>
        </linearGradient>
        <radialGradient id="chartGlow" cx="0.68" cy="0.42" r="0.3">
          <stop offset="0" stop-color="#2b8fa8" stop-opacity="0.6"/>
          <stop offset="1" stop-color="#2b8fa8" stop-opacity="0"/>
        </radialGradient>
      </defs>
      <path role="img" aria-label="Photo: businessman touching a glowing financial chart of monthly growth figures"
        d="M0 118 H1200 V700 Q1200 770 1130 770 Q600 738 70 770 Q0 770 0 700Z" fill="url(#heroTone)"/>
      <path d="M0 118 H1200 V700 Q1200 770 1130 770 Q600 738 70 770 Q0 770 0 700Z" fill="url(#chartGlow)"/>
      <path d="M1200 700 Q1200 770 1130 770 Q600 738 70 770 Q0 770 0 700" fill="none" stroke="var(--blue-line)" stroke-width="6"/>
    </svg>
    <h1 class="hero-title">WELCOME TO<br>VELIM</h1>
    <a class="pill">Get Started</a>

    <form class="quote-panel">
      <h2>GET A QUOTE NOW</h2>
      <div class="quote-fields">
        <div>First Name</div><div>Last Name</div>
        <div>Phone</div><div>Email</div>
      </div>
      <a class="pill">Submit</a>
    </form>
  </section>

  <section class="about">
    <svg class="about-photo" width="427" height="442" role="img" aria-label="Photo: two engineers in hard hats and safety vests inspecting solar panels">
      <defs>
        <linearGradient id="solarTone" x1="0" y1="0" x2="0" y2="1">
          <stop offset="0" stop-color="#7fa6cf"/>
          <stop offset="0.45" stop-color="#2a4f86"/>
          <stop offset="0.78" stop-color="#5a5640"/>
          <stop offset="1" stop-color="#a88c3e"/>
        </linearGradient>
      </defs>
      <rect x="0" y="0" width="352" height="373" fill="url(#solarTone)"/>
      <rect x="369" y="0" width="58" height="373" fill="url(#solarTone)"/>
      <rect x="0" y="388" width="427" height="54" fill="#8a7440"/>
    </svg>
    <h2 class="about-title">ABOUT US</h2>
    <p class="about-copy">Lorem ipsum dolor sit amet, consectetur adipiscing elit, sed do eiusmod tempor incididunt ut labore et dolore magna aliqua. Quis ipsum suspendisse ultrices gravida. Risus commodo viverra maecenas accumsan lacus vel facilisis. Lorem ipsum dolor sit amet, consectetur adipiscing elit, sed do eiusmod tempor incididunt ut labore et dolore magna aliqua. Quis ipsum suspendisse ultrices gravida. Risus commodo viverra maecenas accumsan lacus vel facilisis. Quis ipsum suspendisse ultrices gravida. Risus commodo viverra maecenas accumsan lacus vel facilisis.</p>
    <a class="pill">Submit</a>
  </section>

  <section class="services">
    <h2 class="services-title">SERVICES</h2>
    <div class="service" style="left:98px; top:1890px;">
      <svg width="290" height="290" role="img" aria-label="Photo: man working at a desk with a computer in a bright office">
        <circle cx="145" cy="145" r="143" fill="var(--cream)"/>
        <circle cx="145" cy="145" r="134" fill="#9c9a97"/>
      </svg>
      <p>Advertising</p>
    </div>
    <div class="service" style="left:442px; top:1772px;">
      <svg width="290" height="290" role="img" aria-label="Photo: woman holding a tablet surrounded by projected data">
        <circle cx="145" cy="145" r="143" fill="var(--cream)"/>
        <circle cx="145" cy="145" r="134" fill="#3a5690"/>
      </svg>
      <p>Data Analytics</p>
    </div>
    <div class="service" style="left:805px; top:1890px;">
      <svg width="290" height="290" role="img" aria-label="Photo: glowing globe connecting a network of people">
        <circle cx="145" cy="145" r="143" fill="var(--cream)"/>
        <circle cx="145" cy="145" r="134" fill="#4e6a7c"/>
      </svg>
      <p>Customer Relationship<br>Management</p>
    </div>
  </section>

  <footer>
    <svg class="site-footer" width="1200" height="2655" aria-hidden="true">
      <path d="M0 2420 Q0 2342 70 2342 Q600 2400 1130 2342 Q1200 2342 1200 2420 V2655 H0Z" fill="var(--navy)"/>
      <path d="M0 2420 Q0 2342 70 2342 Q600 2400 1130 2342 Q1200 2342 1200 2420" fill="none" stroke="var(--blue-line)" stroke-width="6"/>
    </svg>
    <div class="footer-content">
      <div class="brand site-footer-brand">VELIM</div>
      <nav class="footer-nav"><span>HOME</span><span>ABOUT</span><span>SERVICES</span><span>CONTACT</span></nav>
      <div class="social"><span>Kestro</span><span>Bramli</span><span>Lumet</span><span>Workly</span></div>
      <div class="footer-rule"></div>
      <p class="copyright">© Copyrights 2023 Velim | All Rights Reserved</p>
    </div>
  </footer>
</body>
</html>
```